Spanish Student Needs a Cover for his PhD Dissertation

Hi everyone :) So, I'm a Corneal surgeon currently finishing my PhD, with a dissertation focused on the evaluation of quality of life in patients affected by a disease called Keratoconus. Just so you know, Keratoconus is a condition in which the cornea (the frontal part of the way) gets thin and bulgy and it decreases vision. What I did during my PhD was designing a questionnaire for evaluating quality of life in this kind of patients.
I need to design a hard cover for my dissertation, which is 200 sheets long. I like kind of minimalistic and geometric designs but I am totally open to suggestions. What needs to be in the cover is the name of the dissertation "Diseño, desarrollo y validación de una encuesta para evaluar el compromiso visual y emocional subjetivos en pacientes con Queratocono" and my name, "Iker Zurmendi". The other thing that needs to go there is the logo of my university (Universidad de Montehierro). Aside from that, anything else is up to the designer. It would be important to use the kind of "red" color I am using in the dissertation. I am attaching the frontal page of my dissertation so you know what kind of design and colors I am using.
In the back part, of the cover, there should be this small inscription: "Iker Zurmendi, MD, es un Oftalmólogo Subespecialista en Cirugía Refractiva de la Universidad Tecnológica Cordillerana (Colombia) y la Universidad de Montehierro (España). Actualmente se desempeña como miembro del Departamento de Córnea y Cirugía Refractiva de la Clínica de Oftalmología Miraluz y como director de su propia compañía de emprendimiento médico Silver Heron Surgical". Please leave a space to place my picture; I will have it taken this week so I don't have it right now, you can just leave the blank spot and I will include it later
The size of the pages is standard "letter" size.
Thanks a lot!

Target Market(s)

PhD Scholars

Font styles to use
Serif

Requirements
Must have
• The "red" color I use on my font. It must be formal but "young".
Nice to have
• I like to keep the design clean, kind of "formal with a young" touch so to speak. I really like gray colors, so it would be nice to have broad areas of gray. I love geometrical designs.
I have uploaded a very early version a friend of mine made (it even had a different title); this can be a starting point for you to work on, but I am more than open to suggestions and new ideas.
Should not have
• Please don't use my whole name, Iker Zurmendi is fine. I don't like ALL CAPITALS.

```html
<!DOCTYPE html>
<html lang="es">
<head>
<meta charset="utf-8">
<title>Cubierta de tesis – Queratocono</title>
<link href="https://fonts.googleapis.com/css2?family=Cormorant+Garamond:wght@300;400;500;600;700&family=Crimson+Pro:wght@400;500&family=Libre+Caslon+Text&display=swap" rel="stylesheet">
<style>
  :root{
    --stage:#231f20;
    --red:#cc1f26;
    --blue:#2d4e9f;
    --white:#ffffff;
    --ink:#231f20;
  }
  *{margin:0;padding:0;box-sizing:border-box}
  html,body{width:1200px;height:1200px;overflow:hidden;background:var(--stage)}
  .cover{position:absolute;left:51px;top:253px;width:1098px;height:694px;display:flex}
  .back{width:321px;height:100%;background:var(--red);padding:47px 30px 0 46px;overflow:hidden}
  .back p{font-family:"Crimson Pro",Georgia,serif;font-weight:500;font-size:11px;line-height:14.7px;color:var(--white);margin-bottom:4px;width:240px;hyphens:auto}
  .spine{position:relative;width:240px;height:100%;background:var(--blue);color:var(--white)}
  .author-photo{position:absolute;left:23px;top:44px;width:118px;height:118px;border-radius:50%;background:var(--white);display:flex;align-items:center;justify-content:center;font-family:"Libre Caslon Text",Georgia,serif;font-size:15px;color:var(--ink)}
  .author-bio{position:absolute;left:23px;top:192px;width:160px;font-family:"Crimson Pro",Georgia,serif;font-size:11px;line-height:15.8px}
  .spine-title{position:absolute;left:220px;top:220px;height:230px;writing-mode:vertical-rl;font-family:"Crimson Pro",Georgia,serif;font-size:7px;line-height:8.5px}
  .spine-author{position:absolute;left:221px;top:590px;writing-mode:vertical-rl;font-family:"Crimson Pro",Georgia,serif;font-size:12px}
  .front{width:537px;height:100%;background:var(--white)}
  .front svg{display:block}
  .t{font-family:"Cormorant Garamond",Garamond,serif;fill:var(--white)}
  .uni-name{font-family:"Crimson Pro",Georgia,serif;font-weight:500;fill:var(--red)}
  .author-name{font-family:"Cormorant Garamond",Garamond,serif;fill:var(--ink)}
</style>
</head>
<body>
<div class="cover">
  <section class="back" lang="la">
    <p>Lorem ipsum dolor sit amet, consectetuer adipiscing elit, sed diam nonummy nibh euismod tincidunt ut laoreet dolore magna aliquam erat volutpat. Ut wisi enim ad minim veniam, quis nostrud exerci tation ullamcorper suscipit lobortis nisl ut aliquip ex ea commodo consequat. Duis autem vel eum iriure dolor in hendrerit in vulputate velit esse molestie consequat, vel illum dolore eu feugiat nulla facilisis at vero eros et accumsan et iusto odio dignissim qui blandit praesent luptatum zzril delenit augue duis dolore te feugait nulla facilisi.</p>
    <p>Lorem ipsum dolor sit amet, cons ectetuer adipiscing elit, sed diam nonummy nibh euismod tincidunt ut laoreet dolore magna aliquam erat volutpat. Ut wisi enim ad minim veniam, quis nostrud exerci tation ullamcorper suscipit lobortis nisl ut aliquip ex ea commodo consequat.</p>
    <p>Lorem ipsum dolor sit amet, consectetuer adipiscing elit, sed diam nonummy nibh euismod tincidunt ut laoreet dolore magna aliquam erat volutpat. Ut wisi enim ad minim veniam, quis nostrud exerci tation ullamcorper suscipit lobortis nisl ut aliquip ex ea commodo consequat. Duis autem vel eum iriure dolor in hendrerit in vulputate velit esse molestie consequat, vel illum dolore eu feugiat nulla facilisis at vero eros et accumsan et iusto odio dignissim qui blandit praesent luptatum zzril delenit augue duis dolore te feugait nulla facilisi.</p>
    <p>Lorem ipsum dolor sit amet, cons ectetuer adipiscing elit, sed diam nonummy nibh euismod tincidunt ut laoreet dolore magna aliquam erat volutpat. Ut wisi enim ad minim veniam, quis nostrud exerci tation ullamcorper suscipit lobortis nisl ut aliquip ex ea commodo consequat.</p>
    <p>Lorem ipsum dolor sit amet, consectetuer adipiscing elit, sed diam nonummy nibh euismod tincidunt ut laoreet dolore magna aliquam erat volutpat. Ut wisi enim ad minim veniam, quis nostrud exerci</p>
  </section>

  <section class="spine">
    <div class="author-photo">authors photo</div>
    <p class="author-bio">Iker Zurmendi, MD, es un Oftalmólogo Subespecialista en Cirugía Refractiva de la Universidad Tecnológica Cordillerana (Colombia) y la Universidad de Montehierro (España). Actualmente se desempeña como miembro del Departamento de Córnea y Cirugía Refractiva de la Clínica de Oftalmología Miraluz y como director de su propia compañía de emprendimiento médico Silver Heron Surgical</p>
    <p class="spine-title">Diseño, desarrollo y validación de una encuesta para evaluar el compromiso visual y emocional subjetivos en pacientes con Queratocono</p>
    <p class="spine-author">Iker Zurmendi</p>
  </section>

  <section class="front">
    <svg width="537" height="694" viewBox="0 0 537 694">
      <defs>
        <linearGradient id="illustrationTone" x1="0" y1="0" x2="1" y2="1">
          <stop offset="0" stop-color="#f5d28a"/>
          <stop offset="1" stop-color="#e9a35c"/>
        </linearGradient>
      </defs>
      <rect class="red-band" x="0" y="188" width="537" height="399" fill="var(--red)"/>
      <polygon class="blue-wedge" points="0,156 377,19 377,356 0,221" fill="var(--blue)"/>
      <rect class="illustration-area" x="130" y="46" width="222" height="276" fill="url(#illustrationTone)" role="img" aria-label="Ilustración anatómica de un ojo en corte lateral"/>
      <text class="t" x="56" y="381" font-size="80" font-weight="600">Diseño,</text>
      <text class="t" x="56" y="423" font-size="25" font-weight="300">desarrollo y validación</text>
      <text class="t" x="56" y="454" font-size="26" font-weight="600">de una encuesta para</text>
      <text class="t" x="56" y="486" font-size="26" font-weight="600">evaluar el compromiso visual</text>
      <text class="t" x="56" y="516" font-size="19" font-weight="300">y emocional subjetivos en pacientes con</text>
      <text class="t" x="56" y="563" font-size="47" font-weight="500">QUERATOCONO</text>
      <circle cx="105" cy="628" r="20" fill="none" stroke="var(--red)" stroke-width="1.2"/>
      <text class="uni-name" x="105" y="668" font-size="11.5" text-anchor="middle">Universidad de Montehierro</text>
      <line x1="289" y1="613" x2="289" y2="694" stroke="var(--ink)" stroke-width="1"/>
      <text class="author-name" x="300" y="651" font-size="29">Iker Zurmendi</text>
    </svg>
  </section>
</div>
</body>
</html>
```